Business card for Eyelash extension salon in Beverly Hills,California USA

We need new business card for our salon in Beverly Hills. The salon name is 'Lashvera' . We would like to have...Business name: Lashvera Name of person: will provide later Address 4720 N.Alder Crest Ave Beverly Hills , CA 90210 Phone: will provide later (Text only) Web: www.lashverastudio.example Snapgrid icon, Circlebook icon follow us for seasonal campaign and news @lashverastudiolounge Design should look elegant, high-end, clean, simple, cohesive with my brand. Please refer my brand board. Business name color will be metallic bronzy color. Im thinking grey background or white background. Thanks

Target Market(s)

25-35. Gender neutral. People who are in Entertainment business industry.
This is High-end Eyelash extension salon in Beverly Hills

Industry/Entity Type

Beauty Salon

Contact Information for Business Card

Business name: Lashvera
Name of person: will provide later
Address 4720 N.Alder Crest Ave Beverly Hills , CA 90210
Phone: will provide later (Text only)
Web: www.lashverastudio.example
Snapgrid icon, Circlebook icon
follow us for seasonal campaign and news @lashverastudiolounge

Requirements
Must have
• Beautiful, elegant, clean and simple look but very attractive and modern
Should not have
• We don't like too clutter, too busy designs.

```html
<!DOCTYPE html>
<html lang="en">
<head>
<meta charset="utf-8">
<title>Lashvera Business Card</title>
<link rel="stylesheet" href="https://fonts.googleapis.com/css2?family=Cinzel:wght@700&family=Cormorant+Garamond:wght@300;400&family=Josefin+Sans:wght@300&display=swap">
<style>
  :root {
    --backdrop: #dcdcdc;
    --card-white: #ffffff;
    --card-brown: #86664b;
    --bronze: #7f5c40;
    --rose-gold: #ecc9aa;
    --tag-gold: #c6a383;
    --text-grey: #7a7a7a;
    --label-grey: #a5a5a5;
    --watermark: #efefef;
  }
  * { margin: 0; padding: 0; box-sizing: border-box; }
  html, body {
    width: 1200px;
    height: 960px;
    overflow: hidden;
    background: var(--backdrop);
  }
  .canvas {
    position: relative;
    width: 1200px;
    height: 960px;
  }
  .card {
    position: absolute;
    width: 600px;
    height: 343px;
    overflow: hidden;
  }
  .card--front {
    left: 302px;
    top: 122px;
    background: var(--card-white);
  }
  .card--back {
    left: 299px;
    top: 495px;
    background: var(--card-brown);
  }
  .front__brand-mark {
    position: absolute;
    left: 14px;
    top: 24px;
    font-family: "Cormorant Garamond", serif;
    font-weight: 300;
    font-size: 172px;
    line-height: 1;
    color: var(--watermark);
    white-space: nowrap;
    letter-spacing: 2px;
  }
  .front__person {
    position: absolute;
    left: 72px;
    top: 208px;
  }
  .person__name {
    font-family: "Cinzel", serif;
    font-weight: 700;
    font-size: 22px;
    line-height: 1;
    letter-spacing: 1px;
    color: var(--bronze);
  }
  .person__role {
    margin-top: 3px;
    font-family: "Cinzel", serif;
    font-weight: 700;
    font-size: 13px;
    letter-spacing: 1.5px;
    color: var(--label-grey);
  }
  .front__contact {
    position: absolute;
    left: 348px;
    top: 207px;
    font-family: "Cormorant Garamond", serif;
    font-weight: 400;
    font-size: 14.5px;
    line-height: 18px;
    font-variant-numeric: lining-nums;
    color: var(--text-grey);
    list-style: none;
  }
  .front__contact .contact__phone { margin-top: 4px; }
  .front__social {
    position: absolute;
    left: 72px;
    top: 262px;
    font-family: "Cormorant Garamond", serif;
    font-weight: 400;
    font-size: 13px;
    line-height: 18px;
    color: var(--text-grey);
  }
  .social__networks {
    display: flex;
    gap: 16px;
    list-style: none;
  }
  .social__network {
    display: flex;
    align-items: center;
    gap: 6px;
  }
  .social__dot {
    width: 8px;
    height: 8px;
    border-radius: 50%;
    background: var(--bronze);
  }
  .back__brand {
    position: absolute;
    left: 0;
    top: 118px;
    width: 100%;
    text-align: center;
    font-family: "Cormorant Garamond", serif;
    font-weight: 300;
    font-size: 92px;
    line-height: 1;
    color: var(--rose-gold);
  }
  .back__location {
    position: absolute;
    left: 295px;
    top: 237px;
    font-family: "Josefin Sans", sans-serif;
    font-weight: 300;
    font-size: 12px;
    letter-spacing: 2.2px;
    color: var(--tag-gold);
  }
</style>
</head>
<body>
<main class="canvas">
  <section class="card card--front" aria-label="Card front">
    <div class="front__brand-mark" aria-hidden="true">Lashvera</div>
    <div class="front__person">
      <p class="person__name">MAREN</p>
      <p class="person__role">OWNER</p>
    </div>
    <ul class="front__contact">
      <li>4720 N.Alder Crest Ave</li>
      <li>Beverly Hills, CA 90210</li>
      <li class="contact__phone">310.555.0142</li>
      <li>hello@lashverastudio.example</li>
      <li>www.lashverastudio.example</li>
    </ul>
    <div class="front__social">
      <p class="social__invite">Follow us for seasonal campaigns &amp; news</p>
      <ul class="social__networks">
        <li class="social__network"><span class="social__dot" aria-hidden="true"></span>Snapgrid</li>
        <li class="social__network"><span class="social__dot" aria-hidden="true"></span>Circlebook</li>
      </ul>
      <p class="social__handle">@lashverastudiolounge</p>
    </div>
  </section>
  <section class="card card--back" aria-label="Card back">
    <h1 class="back__brand">Lashvera</h1>
    <p class="back__location">BEVERLY HILLS</p>
  </section>
</main>
</body>
</html>
```